Business Card Design Project

We need a Business Card for an Mechanical Engineering firm in Singapore. The design should be Modern & Technical looking, yet eye catching.

Our company deals in Cutting Tools & Machine Accessories for the Manufacturing Industries such as Oil & Gas, Aero Space, etc... For more information on our Company, you can either email me or view our website www.torvalen.com.sg.

We are trying to revamp our image to give our consumers a fresh new perspective to our company, so we welcome all ideas.

Industry/Entity Type

Business

Requirements
Must have
• Must incorporate New Company Logo into the card as shown in Uploaded file.

```html
<!DOCTYPE html>
<html lang="en">
<head>
<meta charset="utf-8">
<title>Torvalen Tools — Business Card</title>
<link rel="stylesheet" href="https://fonts.googleapis.com/css2?family=Open+Sans:wght@400;600;700&display=swap">
<style>
  :root {
    --page-bg: #d9d9d9;
    --card-dark: #231f20;
    --card-light: #ffffff;
    --brand-red: #8e1b1f;
    --ink: #2b2b2b;
    --ink-soft: #555555;
    --on-dark: #ffffff;
  }
  * { box-sizing: border-box; margin: 0; padding: 0; }
  html, body { width: 1200px; height: 951px; overflow: hidden; }
  body {
    background: var(--page-bg);
    font-family: "Open Sans", Arial, sans-serif;
    position: relative;
  }
  .card {
    position: absolute;
    left: 290px;
    width: 620px;
    height: 375px;
    border-radius: 22px;
    overflow: hidden;
  }
  .card--back { top: 60px; background: var(--card-dark); }
  .card--front { top: 516px; background: var(--card-light); box-shadow: 0 2px 10px rgba(0,0,0,.12); }

  .wordmark {
    display: flex;
    align-items: center;
    gap: 14px;
    font-weight: 700;
    letter-spacing: 1px;
    text-transform: uppercase;
  }
  .wordmark__dot { width: 22px; height: 22px; border-radius: 50%; background: var(--brand-red); }

  .card--back .wordmark {
    position: absolute; left: 0; right: 0; top: 135px;
    justify-content: center;
    color: var(--on-dark);
    font-size: 46px;
  }
  .card--back .web {
    position: absolute; left: 0; right: 0; top: 262px;
    text-align: center;
    color: var(--on-dark);
    font-size: 19px;
    letter-spacing: .5px;
  }

  .swoosh { position: absolute; inset: 0; width: 100%; height: 100%; }

  .person { position: absolute; left: 88px; top: 78px; }
  .person__name { font-size: 22px; color: var(--ink); font-weight: 400; }
  .person__role { font-size: 17px; color: var(--brand-red); margin-top: 2px; }

  .card--front .wordmark {
    position: absolute; right: 48px; top: 110px;
    color: var(--ink-soft);
    font-size: 32px;
  }

  .address {
    position: absolute; left: 48px; top: 255px;
    display: flex; gap: 10px;
    font-size: 18px; line-height: 1.3; color: var(--ink);
  }
  .contacts {
    position: absolute; left: 330px; top: 236px;
    list-style: none;
    font-size: 18px; line-height: 1.3; color: var(--ink);
  }
  .contacts li { display: flex; align-items: center; gap: 10px; }
  .icon { width: 16px; height: 16px; flex: none; fill: var(--brand-red); }
  .address .icon { margin-top: 3px; }
</style>
</head>
<body>

  <section class="card card--back" aria-label="Card back">
    <div class="wordmark"><span class="wordmark__dot"></span>Torvalen Tools</div>
    <p class="web">www.torvalentools.com</p>
  </section>

  <section class="card card--front" aria-label="Card front">
    <svg class="swoosh" viewBox="0 0 620 375" aria-hidden="true">
      <path d="M0 95 C20 45 60 10 130 0 L0 0 Z" fill="var(--brand-red)"/>
      <path d="M0 112 C25 55 70 18 150 0" fill="none" stroke="var(--card-dark)" stroke-width="5"/>
      <path d="M620 230 C600 300 560 345 470 375 L620 375 Z" fill="var(--brand-red)"/>
      <path d="M620 205 C598 290 548 340 440 375" fill="none" stroke="var(--card-dark)" stroke-width="6"/>
    </svg>

    <div class="person">
      <p class="person__name">Marcus Lindqvar</p>
      <p class="person__role">manager</p>
    </div>

    <div class="wordmark"><span class="wordmark__dot"></span>Torvalen Tools</div>

    <div class="address">
      <svg class="icon" viewBox="0 0 16 16" aria-hidden="true"><path d="M8 1 L15 8 H13 V15 H10 V10 H6 V15 H3 V8 H1 Z"/></svg>
      <p>4100 Harlow Pine Rd.<br>Dalton, TX 78045</p>
    </div>

    <ul class="contacts">
      <li><svg class="icon" viewBox="0 0 16 16" aria-hidden="true"><path d="M4 1 L6.5 5 L5 6.5 C6 9 7 10 9.5 11 L11 9.5 L15 12 L13 15 C7 15 1 9 1 3 Z"/></svg>512-555-0140</li>
      <li><svg class="icon" viewBox="0 0 16 16" aria-hidden="true"><rect x="4" y="1" width="8" height="14" rx="1.5"/></svg>512-555-0141</li>
      <li><svg class="icon" viewBox="0 0 16 16" aria-hidden="true"><path d="M1 4 H15 V13 H1 Z M1 4 L8 9 L15 4" /></svg>info@torvalentools.com</li>
      <li><svg class="icon" viewBox="0 0 16 16" aria-hidden="true"><circle cx="8" cy="8" r="7"/></svg>www.torvalentools.com</li>
    </ul>
  </section>

</body>
</html>
```